Brindlewick Solutions Ltd

I'd like to create a company letterhead for the attached logo in word format.

I'd like to emphasis the icon in large translucent state from the left corner and ensure that the letterhead colouring matches the colour palette of the current logo with a contrast so it's clear to see. I've attached a copy of our sister company page on the app for reference.

```html
<!DOCTYPE html>
<html lang="en">
<head>
<meta charset="utf-8">
<title>Brindlewick Solutions Ltd — Letterhead</title>
<link rel="stylesheet" href="https://fonts.googleapis.com/css2?family=Montserrat:wght@400&family=Arimo:wght@400&family=Mulish:wght@700;800&family=PT+Sans+Narrow&display=swap">
<style>
  :root {
    --teal: #00bda6;
    --ink: #555555;
    --muted: #8a8a8a;
    --band: #9b9b9b;
    --paper: #ffffff;
    --backdrop: #e2e2e2;
  }
  * { margin: 0; padding: 0; box-sizing: border-box; }
  html, body { width: 1200px; height: 1200px; overflow: hidden; background: var(--backdrop); }
  .letterhead {
    position: absolute; left: 233px; top: 81px;
    width: 734px; height: 1038px;
    background: var(--paper); overflow: hidden;
  }
  .brand { position: absolute; left: 65px; top: 42px; display: flex; align-items: center; gap: 10px; }
  .brand-dot { width: 56px; height: 56px; border-radius: 50%; background: var(--teal); }
  .brand-name {
    font-family: "Montserrat", sans-serif; font-weight: 400;
    font-size: 32px; line-height: 1; color: var(--teal); letter-spacing: -0.5px;
  }
  .brand-sub {
    font-family: "Montserrat", sans-serif; font-weight: 400;
    font-size: 9px; letter-spacing: 7.4px; color: var(--muted); margin-top: 4px;
  }
  .salutation {
    position: absolute; left: 67px; top: 318px;
    font-family: "Mulish", sans-serif; font-weight: 800; font-size: 17px; color: var(--ink);
  }
  .letter-body { position: absolute; left: 65px; top: 364px; width: 604px; }
  .letter-body p {
    font-family: "Arimo", sans-serif; font-size: 12.3px; line-height: 15.1px;
    color: var(--ink); margin-bottom: 13.5px;
  }
  .closing {
    position: absolute; left: 67px; top: 678px;
    font-family: "Mulish", sans-serif; font-weight: 700; font-size: 10px; color: var(--ink);
  }
  .signature {
    position: absolute; left: 84px; top: 726px;
    font-family: "PT Sans Narrow", sans-serif; font-size: 20px; letter-spacing: -1px; color: var(--ink);
  }
  .corner-art { position: absolute; left: 0; bottom: 0; width: 734px; height: 200px; }
  .contact-line {
    position: absolute; left: 175px; bottom: 10px;
    display: flex; align-items: center; gap: 6px;
    font-family: "Arimo", sans-serif; font-size: 11px; color: #ffffff; white-space: nowrap;
  }
  .contact-line svg { width: 10px; height: 10px; }
  .contact-line .gap { margin-left: 6px; }
</style>
</head>
<body>
<main class="letterhead">
  <header class="brand">
    <span class="brand-dot"></span>
    <div>
      <div class="brand-name">Brindlewick</div>
      <div class="brand-sub">SOLUTIONS LTD</div>
    </div>
  </header>

  <h1 class="salutation">Dear Mr. Harlow,</h1>

  <section class="letter-body">
    <p>Lorem ipsum dolor sit amet, consectetuer adipiscing elit, sed diam nonmmy nibh euismod tincidunt ut laor eet dolore magna aliquam erat volutpat. Ut wisi enim ad minim veniam, quis nostrud exerci tationmcorper suscipit lobortis nisl ut aliquip ex ea commodo consequat. Duis autem vel eum iriure dolor in hendrerit in vulputate velit esse molestie consequat, vel illum dolore eu feugiat</p>
    <p>Rorem ipsum dolor sit amet, consectetuer adipiscing elit, sed diam nonmmy nibh euismod tincidunt ut laor eet dolore magna aliquam erat volutpat. Ut wisi enim ad minim veniam, quis nostrud exerci tationmcorper suscipit lobortis nisl ut aliquip ex ea commodo consequat. Duis autem vel eum iriure dolor in hendrerit in vulputate velit esse molest</p>
    <p>Dorem ipsum dolor sit amet, consectetuer adipiscing elit, sed diam nonmmy nibh euismod tincidunt ut laor eet dolore magna aliquam erat volutpat. Ut wisi enim ad minim veniam, quis nostrud exerci tationmcorper suscipit lobortis nisl ut aliquip ex ea commodo consequat. Duis autem vel eum iriure dolor in hendrerit in suscipit lobortis nisl ut aliquip ex ea commodo consequat. Duis autem vel eum iriure dolor in hendrerit in vulputate velit esse molestie consequat, vel illum</p>
    <p>Sorem ipsum dolor sit amet, consectetuer adipiscing elit, sed diam nonmmy nibh euismod tincidunt ut laor eet dolore magna aliquam erat volutpat. Ut wisi enim ad minim veniam, quis nostrud exerci tationmcorper suscipit lobortis nisl ut aliquip ex ea commodo consequat. Duis autem vel eum iriure dolor in</p>
  </section>

  <p class="closing">Sincerely,</p>
  <p class="signature">Tomas Verhey</p>

  <svg class="corner-art" viewBox="0 0 734 200" aria-hidden="true">
    <path d="M161 168 H734 V200 H0 Z" fill="var(--band)"/>
    <circle cx="72" cy="100" r="106" fill="var(--paper)"/>
    <circle cx="72" cy="100" r="99" fill="var(--teal)"/>
  </svg>

  <footer class="contact-line">
    <span>Your address, city, state, ZIP 0000 &nbsp;|</span>
    <svg viewBox="0 0 10 10" class="gap"><path d="M2 1 L4 3 L3 4 Q4 6 6 7 L7 6 L9 8 L8 9 Q3 9 1 2 Z" fill="#fff"/></svg>
    <span>123-456-2100</span>
    <svg viewBox="0 0 10 10" class="gap"><rect x="0.5" y="2" width="9" height="6" fill="#fff"/><path d="M0.5 2 L5 5.5 L9.5 2" stroke="var(--band)" stroke-width="0.8" fill="none"/></svg>
    <span>youremail@mailbox.com</span>
    <svg viewBox="0 0 10 10" class="gap"><circle cx="5" cy="5" r="4.5" fill="#fff"/><path d="M1 5 H9 M5 1 Q2.5 5 5 9 M5 1 Q7.5 5 5 9" stroke="var(--band)" stroke-width="0.7" fill="none"/></svg>
    <span>www.yourwebsite.com</span>
  </footer>
</main>
</body>
</html>
```